Accounting firm needing business card / letterhead designed
Marcus L. Trenholm, CPA
marcus@veltrowledger.com
www.veltrowledger.com
842 E Alder Ave Harlow Bend, IN 43827
555-562-0974

```html
<!DOCTYPE html>
<html lang="en">
<head>
<meta charset="utf-8">
<title>Veltro Ledger — Business Card</title>
<link href="https://fonts.googleapis.com/css2?family=Roboto:wght@400;700&family=Roboto+Condensed:wght@700&display=swap" rel="stylesheet">
<style>
  :root {
    --backdrop: #e8e5e0;
    --paper: #f7f7f6;
    --navy: #252060;
    --lime: #8dc63f;
    --white: #ffffff;
  }
  * { margin: 0; padding: 0; box-sizing: border-box; }
  html, body { width: 1200px; height: 960px; overflow: hidden; }
  body { background: var(--backdrop); font-family: "Roboto", Arial, sans-serif; position: relative; }

  .card { position: absolute; width: 600px; height: 343px; box-shadow: 0 2px 5px rgba(0,0,0,.25); overflow: hidden; }

  .card-front { left: 314px; top: 113px; background: var(--paper); }
  .front-brand-panel { position: absolute; left: 0; top: 0; width: 323px; height: 100%; display: flex; align-items: center; justify-content: center; }
  .brand-name-front { color: var(--navy); font-weight: 700; font-size: 31px; letter-spacing: 0.04em; text-transform: uppercase; margin-top: -34px; }

  .front-info-panel { position: absolute; left: 326px; top: 0; right: 0; height: 100%; background: var(--navy); }
  .divider { position: absolute; left: 318px; top: 0; width: 30px; height: 100%; }

  .person-name { position: absolute; left: 44px; top: 68px; font-family: "Roboto Condensed", Arial, sans-serif; font-weight: 700; font-size: 21px; color: var(--lime); white-space: nowrap; }
  .address { position: absolute; left: 44px; top: 168px; color: var(--white); font-size: 14px; line-height: 18px; }
  .contact-list { position: absolute; left: 44px; top: 215px; list-style: none; color: var(--white); font-size: 14px; line-height: 19px; }
  .contact-list li { display: flex; align-items: center; gap: 8px; }
  .contact-list svg { width: 13px; height: 13px; fill: var(--lime); flex: none; }

  .card-back { left: 311px; top: 472px; background: var(--lime); text-align: center; }
  .brand-name-back { position: absolute; left: 0; right: 0; top: 112px; color: var(--white); font-weight: 700; font-size: 56px; letter-spacing: 0.04em; text-transform: uppercase; }
  .back-web { position: absolute; left: 0; right: 0; top: 282px; color: var(--white); font-size: 14px; letter-spacing: 0.45em; }
</style>
</head>
<body>
  <section class="card card-front">
    <div class="front-brand-panel">
      <span class="brand-name-front">Veltro Ledger</span>
    </div>
    <div class="front-info-panel">
      <p class="person-name">Marcus L. Trenholm, CPA</p>
      <p class="address">842 E Alder Ave<br>Harlow Bend, IN 43827</p>
      <ul class="contact-list">
        <li><svg viewBox="0 0 16 16"><path d="M3.6 1.2 6 3.6c.4.4.4 1 0 1.4L4.9 6.1c.9 2 2.9 4 5 5l1.1-1.1c.4-.4 1-.4 1.4 0l2.4 2.4c.4.4.4 1 0 1.4l-1.3 1.3C10.3 16.2.2 6 1 2.5L2.2 1.2c.4-.4 1-.4 1.4 0z"/></svg>555-562-0974</li>
        <li><svg viewBox="0 0 16 16"><path d="M1 3h14v1.2L8 8.6 1 4.2z"/><path d="M1 5.6l7 4.4 7-4.4V13H1z"/></svg>marcus@veltrowledger.com</li>
        <li><svg viewBox="0 0 16 16"><circle cx="8" cy="8" r="7"/><path d="M4 5c1.5 0 2 1 3 1.5S7 9 5.5 9 4 11 4.5 12.5M10 2.5c0 1.5 1 2 2 2s1.5 1.5 1 3-2 1-2.5 2.5" stroke="#252060" stroke-width="1.2" fill="none"/></svg>www.veltrowledger.com</li>
      </ul>
    </div>
    <svg class="divider" viewBox="0 0 30 343" aria-hidden="true">
      <rect x="4" y="0" width="8" height="343" fill="#252060"/>
      <polyline points="5,0 5,70 15,82 5,94 5,343" fill="none" stroke="#8dc63f" stroke-width="3"/>
      <polygon points="6.5,72 16,82 6.5,92 12,82" fill="#252060"/>
      <polygon points="8,0 8,71 17.5,82 8,93 8,343 30,343 30,0" fill="#252060"/>
    </svg>
  </section>

  <section class="card card-back">
    <span class="brand-name-back">Veltro Ledger</span>
    <p class="back-web">www.veltrowledger.com</p>
  </section>
</body>
</html>
```